Garlic Farm for Farm Sales/Restaurant sales

Need a professional, but appealing to agriculture world. We are selling 27 kinds of Organic Garlic from a farm in Simla,CO. I have uploaded logo and business information-we are going to need a template, because I will need to use it for four separate people.
-We are trying to appeal to Farm to table restaurants
-As well as growers/farmers

Target Market(s)

Agriculture Sales/Restaurants-Organic

Industry/Entity Type

Agriculture

Contact Information for Business Card

Want it to look more unique then your average kelto stock card- I want it to look amazing

Font styles to use
Sans Serif

Colors
0455a3
ec1f27
fbed22
ffffff

Requirements
Must have
• Just be creative
Nice to have
• Colorful
Should not have
• plain

```html
<!DOCTYPE html>
<html lang="en">
<head>
<meta charset="utf-8">
<title>Prairie Bulb Farm – Business Card</title>
<link rel="stylesheet" href="https://fonts.googleapis.com/css2?family=PT+Sans:ital,wght@0,400;0,700;1,400;1,700&display=swap">
<style>
  :root {
    --backdrop: #666666;
    --card-light: #f4f4f4;
    --card-wine: #971c37;
    --brand-red: #c0102c;
    --brand-navy: #0d2a5c;
    --ink: #1a1a1a;
    --white: #ffffff;
  }
  * { margin: 0; padding: 0; box-sizing: border-box; }
  html, body { width: 1200px; height: 900px; overflow: hidden; }
  body {
    background: var(--backdrop);
    font-family: "PT Sans", "Myriad Pro", Arial, sans-serif;
    position: relative;
  }
  .card {
    position: absolute;
    top: 300px;
    width: 441px;
    height: 272px;
    border-radius: 10px;
  }
  .card--front { left: 152px; background: var(--card-light); }
  .card--back  { left: 622px; background: var(--card-wine); }

  .brand {
    position: absolute;
    display: flex;
    flex-direction: column;
    align-items: center;
    gap: 10px;
  }
  .card--front .brand { left: 24px; top: 68px; width: 190px; }
  .card--back .brand { left: 0; right: 0; top: 64px; }
  .brand__mark {
    width: 78px; height: 78px; border-radius: 50%;
  }
  .card--front .brand__mark { background: var(--brand-red); }
  .card--back .brand__mark { background: var(--white); }
  .brand__name {
    font-weight: 700;
    font-size: 26px;
    line-height: 1;
    white-space: nowrap;
  }
  .card--front .brand__name { color: var(--brand-navy); }
  .card--back .brand__name { color: var(--white); }

  .contact {
    position: absolute;
    left: 236px;
    top: 48px;
    color: var(--ink);
  }
  .contact__name {
    font-size: 23px;
    font-weight: 700;
    font-style: italic;
    color: var(--brand-red);
    line-height: 1;
  }
  .contact__role {
    font-size: 15px;
    font-style: italic;
    margin-top: 6px;
  }
  .contact__list { list-style: none; margin-top: 16px; }
  .contact__item {
    display: flex; align-items: center; gap: 5px;
    font-size: 14px; line-height: 18px;
  }
  .contact__icon { width: 12px; height: 12px; flex: none; fill: var(--brand-red); }
  .contact__address {
    font-style: normal; font-size: 14px; line-height: 18px; margin-top: 12px;
  }
</style>
</head>
<body>
  <section class="card card--front">
    <div class="brand">
      <span class="brand__mark"></span>
      <span class="brand__name">Prairie Bulb Farm</span>
    </div>
    <div class="contact">
      <p class="contact__name">Dana Ortiz</p>
      <p class="contact__role">Owner</p>
      <ul class="contact__list">
        <li class="contact__item">
          <svg class="contact__icon" viewBox="0 0 12 12" aria-hidden="true"><path d="M1 4c0-2 1-3 5-3s5 1 5 3H8.5V3h-5v1zM3 5h6l2 5H1z"/></svg>
          555-014-2278
        </li>
        <li class="contact__item">
          <svg class="contact__icon" viewBox="0 0 12 12" aria-hidden="true"><path d="M3 1h5l1 1v2h2v7H1V4h2zM4 2v2h4V2zM3 6v1h6V6zM3 8v1h6V8z"/></svg>
          (555)-014-9
        </li>
        <li class="contact__item">
          <svg class="contact__icon" viewBox="0 0 12 12" aria-hidden="true"><path d="M0 2h12v1L6 7 0 3zM0 4.3l6 4 6-4V10H0z"/></svg>
          hello@prairiebulb.com
        </li>
        <li class="contact__item">
          <svg class="contact__icon" viewBox="0 0 12 12" aria-hidden="true"><circle cx="6" cy="6" r="6"/><path d="M3 4c1 0 2 1 2 2s-1 1-1 3M7 2c0 2 2 2 3 2M8 7c1 0 1 2 0 3" stroke="#f4f4f4" stroke-width="1" fill="none"/></svg>
          www.prairiebulb.com
        </li>
      </ul>
      <address class="contact__address">PO Box 2187,<br>Simla, CO 80835</address>
    </div>
  </section>

  <section class="card card--back">
    <div class="brand">
      <span class="brand__mark"></span>
      <span class="brand__name">Prairie Bulb Farm</span>
    </div>
  </section>
</body>
</html>
```